New Business Cards for Tormin Group

We need a new Business Card to compliment our new logo. We are a vibrant design, manufacture and install business providing recreation areas, public parks and Municipal spaces. We want business cards that are classy, modern and clean.

We have recently changed our logo, and are celebrating our 40th anniversary. We want business cards with a new modern design to reflect our status.

Target Market(s)

Customers

Contact Information for Business Card

We need all the details of our 3 offices as per the business card attached. Please disregard the old logo on the business card, the other three files show our new logo.

Requirements
Must have
• All info as per attached business card but with new logo.
Nice to have

```html
<!DOCTYPE html>
<html lang="en">
<head>
<meta charset="utf-8">
<title>Tormin Group – Business Card</title>
<link rel="stylesheet" href="https://fonts.googleapis.com/css2?family=Lato:wght@400;700&display=swap">
<style>
  :root {
    --page-bg: #5f5f5f;
    --card-bg: #ffffff;
    --brand-red: #e8303a;
    --ink-dark: #3b3b3d;
    --ink-body: #5a5a5c;
    --rule: #6b6b6b;
  }
  * { margin: 0; padding: 0; box-sizing: border-box; }
  html, body {
    width: 1200px; height: 1200px; overflow: hidden;
    background: var(--page-bg);
    font-family: "Lato", Arial, sans-serif;
  }
  .business-card {
    position: absolute; left: 100px; top: 310px;
    width: 1000px; height: 581px;
    background: var(--card-bg);
    border-radius: 36px;
    overflow: hidden;
  }
  .brand {
    position: absolute; left: 44px; top: 70px;
    display: flex; align-items: center; gap: 22px;
  }
  .brand-mark {
    width: 130px; height: 130px; border-radius: 50%;
    background: var(--brand-red);
  }
  .brand-name {
    font-size: 38px; font-weight: 700; color: var(--ink-dark);
    letter-spacing: 1px;
  }
  .person {
    position: absolute; right: 36px; top: 74px; text-align: right;
  }
  .person-name {
    font-size: 34px; font-weight: 400; color: var(--brand-red); line-height: 1.2;
  }
  .person-title {
    font-size: 22px; color: var(--ink-dark); margin-top: 8px;
  }
  .direct-contact {
    position: absolute; right: 36px; top: 236px; text-align: right;
    font-size: 18px; color: var(--ink-dark); line-height: 34px;
  }
  .direct-contact li { list-style: none; display: flex; justify-content: flex-end; align-items: center; gap: 12px; }
  .direct-contact svg { width: 13px; height: 13px; fill: var(--brand-red); }
  .divider {
    position: absolute; left: 40px; right: 35px; top: 336px;
    height: 2px; background: var(--rule);
  }
  .office {
    position: absolute; top: 350px; text-align: right;
    color: var(--ink-body); font-size: 18px; line-height: 30px;
  }
  .office h3 {
    font-size: 24px; font-weight: 400; color: var(--brand-red);
    line-height: 34px; margin-bottom: 4px;
  }
  .office--head { right: 668px; }
  .office--dubai { right: 341px; }
  .office--qatar { right: 35px; top: 354px; }
  .web-tab {
    position: absolute; right: 0; bottom: 0; width: 345px; height: 56px;
  }
  .web-tab svg { position: absolute; inset: 0; width: 100%; height: 100%; }
  .web-tab span {
    position: absolute; right: 36px; top: 50%; transform: translateY(-50%);
    color: #fff; font-size: 18px;
  }
</style>
</head>
<body>
  <article class="business-card">
    <div class="brand">
      <div class="brand-mark"></div>
      <div class="brand-name">TORMIN GROUP</div>
    </div>

    <div class="person">
      <div class="person-name">Samir Haddad</div>
      <div class="person-title">Managing Partner</div>
    </div>

    <ul class="direct-contact">
      <li>+971 (0)50 384 7719
        <svg viewBox="0 0 24 24"><path d="M6.6 10.8a15.1 15.1 0 0 0 6.6 6.6l2.2-2.2a1 1 0 0 1 1-.25 11.4 11.4 0 0 0 3.6.57 1 1 0 0 1 1 1V20a1 1 0 0 1-1 1A17 17 0 0 1 3 4a1 1 0 0 1 1-1h3.5a1 1 0 0 1 1 1c0 1.25.2 2.45.57 3.57a1 1 0 0 1-.25 1z"/></svg>
      </li>
      <li>samir@tormingroup.com
        <svg viewBox="0 0 24 24"><path d="M2 5h20v14H2z" fill="none"/><path d="M2 5h20v2l-10 6L2 7zM2 9l10 6 10-6v10H2z"/></svg>
      </li>
    </ul>

    <div class="divider"></div>

    <section class="office office--head">
      <h3>Head Office</h3>
      <p>P.O. Box: 41820 Abu Dhabi. U.A.E</p>
      <p>Tel No: +971 (0)2 5537201</p>
      <p>Fax No: +971(0)2 5537209</p>
      <p>Email: sales@tormingroup.com</p>
    </section>

    <section class="office office--dubai">
      <h3>Dubai Office</h3>
      <p>P.O. Box: 270415 Dubai, U.A.E</p>
      <p>Tel No: +971 (0)4 386214</p>
      <p>Fax No: +971(0)4 386250</p>
      <p>Email: sales@tormingroup.com</p>
    </section>

    <section class="office office--qatar">
      <h3>Qater Office</h3>
      <p>P.O. Box: 18342 Doha, Qatter</p>
      <p>Tel No: +974 44719308</p>
      <p>Fax No: +971 44925317</p>
      <p>Email: sales@tormingroup.com</p>
    </section>

    <div class="web-tab">
      <svg viewBox="0 0 345 56" preserveAspectRatio="none">
        <path d="M34 0 H345 V56 H0 L22 8 Q26 0 34 0 Z" fill="var(--brand-red)"/>
      </svg>
      <span>www.tormingroup.com</span>
    </div>
  </article>
</body>
</html>
```